Lo Mara Menu Design Project

This project is pretty straight forward. You will be given 3 files which include the following:
1. Our proposed menu
2. Our Company logo
3. A sample menu on what we are looking for design wise

Your job is to create a visually pleasing menu that is simple, clean and fresh. Please refer to our home website for additional information. (www.lomara-eats.com) Must be in eps or equivalent format.

Target Market(s)

20s to 40s

Industry/Entity Type

It Company

Requirements
Must have
• Company log
Must be in EPS format

```html
<!DOCTYPE html>
<html lang="en">
<head>
<meta charset="utf-8">
<title>Lo Mara Menu</title>
<link href="https://fonts.googleapis.com/css2?family=Arimo&family=Open+Sans:wght@400&family=Tinos:wght@700&display=swap" rel="stylesheet">
<style>
:root{
  --backdrop:#5a3420;
  --panel-dark:#151515;
  --panel-mid:#262626;
  --ink:#ffffff;
  --ink-soft:#e6e6e6;
  --accent:#d3261c;
}
*{margin:0;padding:0;box-sizing:border-box}
html,body{width:1200px;height:737px;overflow:hidden;background:var(--backdrop)}
.stage{position:relative;width:1190px;height:731px;transform:scale(1.0084,1.0082);transform-origin:0 0}
.page{position:absolute;top:50px;width:487px;height:630px;
  background:
    repeating-linear-gradient(90deg,rgba(255,255,255,.025) 0 1px,transparent 1px 5px,rgba(0,0,0,.12) 5px 7px,transparent 7px 11px),
    linear-gradient(90deg,var(--panel-dark),var(--panel-mid) 50%,var(--panel-dark));}
.page-left{left:71px}
.page-right{left:612px;width:486px}
.section-title{position:absolute;transform:translateX(-50%);font-family:"Arimo",Arial,sans-serif;font-size:37px;color:var(--ink);white-space:nowrap;line-height:1}
.rule{position:absolute;height:3px;background:var(--accent)}
.item{position:absolute;transform:translateX(-50%);width:200px;text-align:center;color:var(--ink)}
.item-name,.item-price{font-family:"Tinos","Times New Roman",serif;font-weight:700;font-size:10.5px;line-height:13px}
.item-desc{margin-top:5px;font-family:"Open Sans",Arial,sans-serif;font-size:8px;line-height:10.5px;color:var(--ink-soft)}
.brand{position:absolute;left:1022px;top:628px;font-family:"Tinos","Times New Roman",serif;font-weight:700;font-size:17px;color:var(--accent);line-height:1}
</style>
</head>
<body>
<div class="stage">
  <div class="page page-left"></div>
  <div class="page page-right"></div>

  <h2 class="section-title" style="left:313px;top:66px">Chicken</h2>
  <div class="rule" style="left:250px;top:101px;width:127px"></div>

  <div class="item" style="left:158px;top:107px"><p class="item-name">General Tso’s Chicken</p><p class="item-price">$ 11.75</p><p class="item-desc">Crispy dark meat chicken with<br>chili peppers in a spicy tangerine<br>sauce topped with scallions.</p></div>
  <div class="item" style="left:315px;top:133px"><p class="item-name">Orange Chicken</p><p class="item-price">$ 11.95</p><p class="item-desc">Crispy chicken breast with<br>onions and red and green bell<br>peppers in a tangy orange sauce.</p></div>
  <div class="item" style="left:472px;top:105px"><p class="item-name">Kung Pao Chicken</p><p class="item-price">$ 11.95</p><p class="item-desc">Dark meat chicken with red bell<br>peppers, peanuts, and water<br>chestnuts in spicy red sauce.</p></div>
  <div class="item" style="left:226px;top:211px"><p class="item-name">Chicken Lettuce Cups<br>(also known as wraps)</p><p class="item-price">$ 11.75</p><p class="item-desc">Minced white meat chicken with bell<br>peppers, water chestnuts, black mushrooms,<br>pine nuts, and white crunchies. Served with<br>four lettuce cups.</p></div>
  <div class="item" style="left:444px;top:220px"><p class="item-name">Moo Goo Gai Pan</p><p class="item-price">$ 00</p></div>

  <h2 class="section-title" style="left:314px;top:315px">Beef/Pork</h2>
  <div class="rule" style="left:237px;top:350px;width:154px"></div>

  <div class="item" style="left:167px;top:365px"><p class="item-name">Mongolian Beef</p><p class="item-price">$ 12.25</p><p class="item-desc">Flank steak, garlic, ginger, and green<br>onions on a bed of white<br>crunchies.</p></div>
  <div class="item" style="left:311px;top:379px"><p class="item-name">Beef &amp; Broccoli</p><p class="item-price">$ 11.95</p><p class="item-desc">Flank steak, broccoli, and black<br>mushrooms sautéed in a garlic<br>brown sauce.</p></div>
  <div class="item" style="left:467px;top:363px"><p class="item-name">Pepper Steak</p><p class="item-price">$ 11.95</p><p class="item-desc">Flank steak, bell peppers, onions<br>and garlic in black pepper sauce.</p></div>
  <div class="item" style="left:240px;top:467px"><p class="item-name">Sweet &amp; Sour Pork</p><p class="item-price">$ 00</p></div>
  <div class="item" style="left:393px;top:467px"><p class="item-name">Sliced BBQ Pork</p><p class="item-price">$ 8.95</p><p class="item-desc">Tender slices of juicy pork topped<br>with scallions in a barbeque<br>sauce.</p></div>

  <h2 class="section-title" style="left:311px;top:543px">Seafood</h2>
  <div class="rule" style="left:246px;top:578px;width:130px"></div>

  <div class="item" style="left:157px;top:587px"><p class="item-name">Shrimp w/ Snow Peas</p><p class="item-price">$ 13.95</p><p class="item-desc">Large shrimp with snow peas,<br>water chestnuts, carrots, and ginger<br>in a white wine sauce.</p></div>
  <div class="item" style="left:314px;top:613px"><p class="item-name">Scallops w/ black bean sauce</p><p class="item-price">$ 00</p></div>
  <div class="item" style="left:472px;top:586px"><p class="item-name">Fish w/ ginger soy</p><p class="item-price">$ 15.95</p><p class="item-desc">Whole white fish filet steamed<br>with ginger and topped with green<br>onions and cilantro.</p></div>

  <div class="item" style="left:765px;top:81px;width:240px"><p class="item-name">Kung Pao 3 treasures</p><p class="item-price">$ 13.95</p><p class="item-desc">Large shrimp, beef, and chicken breast with<br>scallions, peanuts, water chestnuts, and chili peppers.<br>Prepared mandarin-Style.</p></div>
  <div class="item" style="left:979px;top:81px"><p class="item-name">Honey Walnut Shrimp</p><p class="item-price">$ 13.95</p><p class="item-desc">Lightly crisped savory shrimp with<br>honey-Glazed walnuts.</p></div>

  <h2 class="section-title" style="left:854px;top:171px">Vegetables</h2>
  <div class="rule" style="left:770px;top:210px;width:170px"></div>

  <div class="item" style="left:696px;top:228px"><p class="item-name">Spinach w/ garlic</p><p class="item-price">$ 6.95</p><p class="item-desc">Sautéed spinach with garlic.</p></div>
  <div class="item" style="left:840px;top:242px"><p class="item-name">Bak Choy w/ Mushrooms</p><p class="item-price">$ 6.95</p><p class="item-desc">Baby bokchoy and black<br>mushrooms sautéed in a<br>brown sauce.</p></div>
  <div class="item" style="left:1001px;top:227px"><p class="item-name">Fragrant Vegetables</p><p class="item-price">$ 8.95</p><p class="item-desc">Mixed vegetables with white wine,<br>curry, garlic, black bean, kungpao,<br>or vegetarian sauce.</p></div>
  <div class="item" style="left:770px;top:328px"><p class="item-name">Schezuan String Bean</p><p class="item-price">$ 8.95</p><p class="item-desc">Blue lake green beans and garlic sautéed<br>with pickled szechwan vegetables.</p></div>
  <div class="item" style="left:934px;top:328px;width:220px"><p class="item-name">Spicy Garlic Eggplant</p><p class="item-price">$ 8.95</p><p class="item-desc">Sautéed chinese eggplant, red onions, and<br>scallions in a spicy garlic sauce.</p></div>

  <h2 class="section-title" style="left:854px;top:421px">Noodles</h2>
  <div class="rule" style="left:787px;top:460px;width:135px"></div>

  <div class="item" style="left:696px;top:469px"><p class="item-name">Chow Mein</p><p class="item-price">$ 12.95</p><p class="item-desc">Crispy egg noodles or soft lo mein<br>noodles with large vegetables and<br>chicken, pork, or vegetables.<br>Beef or shrimp instead, add $1.00.</p></div>
  <div class="item" style="left:840px;top:483px"><p class="item-name">Lo Mein</p><p class="item-price">$ 10.95</p><p class="item-desc">Soft lo mein noodles with shredded<br>vegetables and chicken, pork,<br>or vegetables.<br>Beef or shrimp instead, add $1.00.</p></div>
  <div class="item" style="left:1012px;top:467px;width:220px"><p class="item-name">Pad Thai</p><p class="item-price">$ 12.95</p><p class="item-desc">Rice noodles with chicken, shrimp, eggs,<br>onions, and scallions topped<br>with peanuts and cilantro.</p></div>
  <div class="item" style="left:797px;top:593px"><p class="item-name">Singapore Noodles</p><p class="item-price">$ 10.95</p><p class="item-desc">Shrimp, barbeque pork, bean sprouts,<br>onions, egg, and bell peppers with rice noodles<br>in a curry sauce</p></div>
  <div class="item" style="left:960px;top:593px"><p class="item-name">Seafood Noodles</p><p class="item-price">$ 00</p></div>

  <p class="brand">Lo Mara</p>
</div>
</body>
</html>
```